TA BRAMLEY BUSINESS CARD DESIGN PROJECT

We need to utilize our logo that was expertly created on PixelHarbor and now need to match this with a business card design.

```html
<!DOCTYPE html>
<html lang="en">
<head>
<meta charset="UTF-8">
<title>TA Bramley – Business Card</title>
<link href="https://fonts.googleapis.com/css2?family=Poppins:wght@400;600;700&display=swap" rel="stylesheet">
<style>
  :root {
    --brand-blue: #1056a8;
    --card-black: #151515;
    --paper-white: #ffffff;
    --backdrop: #d9dbde;
    --text-light: #f2f2f2;
  }
  * { margin: 0; padding: 0; box-sizing: border-box; }
  html, body { width: 1200px; height: 900px; overflow: hidden; }
  body {
    background: var(--backdrop);
    font-family: "Poppins", sans-serif;
    position: relative;
  }
  .card {
    position: absolute;
    width: 600px;
    height: 343px;
    border-radius: 22px;
    overflow: hidden;
    box-shadow: 0 10px 30px rgba(0,0,0,0.22);
  }
  .card-front {
    left: 300px;
    top: 60px;
    background: var(--brand-blue);
    display: flex;
    align-items: center;
    justify-content: center;
  }
  .brand-name {
    font-weight: 700;
    letter-spacing: 0.12em;
    white-space: nowrap;
  }
  .card-front .brand-name {
    color: var(--paper-white);
    font-size: 64px;
  }
  .card-back {
    left: 300px;
    top: 470px;
    background: var(--card-black);
  }
  .card-back .backdrop-shapes {
    position: absolute;
    inset: 0;
  }
  .card-back .brand-name {
    position: absolute;
    left: 40px;
    top: 150px;
    width: 300px;
    text-align: center;
    color: var(--brand-blue);
    font-size: 36px;
  }
  .contact-block {
    position: absolute;
    left: 380px;
    top: 52px;
    color: var(--text-light);
    font-size: 13px;
    line-height: 1.45;
  }
  .person-name {
    color: var(--brand-blue);
    font-weight: 700;
    font-size: 20px;
    letter-spacing: -0.01em;
    line-height: 1.1;
  }
  .person-title { font-size: 14px; margin-bottom: 26px; }
  .address { margin-bottom: 20px; }
  .contact-line { display: flex; align-items: center; gap: 7px; }
  .contact-line svg { width: 12px; height: 12px; fill: var(--brand-blue); flex: none; }
</style>
</head>
<body>
  <section class="card card-front">
    <span class="brand-name">TA BRAMLEY</span>
  </section>

  <section class="card card-back">
    <svg class="backdrop-shapes" width="600" height="343" viewBox="0 0 600 343">
      <circle cx="150" cy="210" r="222" fill="var(--brand-blue)"/>
      <circle cx="140" cy="218" r="214" fill="var(--paper-white)"/>
    </svg>
    <span class="brand-name">TA BRAMLEY</span>
    <div class="contact-block">
      <div class="person-name">DANA WHITLOW</div>
      <div class="person-title">Director</div>
      <div class="address">2418 Harbor Lane<br>14-16. 2 floor 7.</div>
      <div class="contact-line">
        <svg viewBox="0 0 24 24"><path d="M6.6 10.8a15.1 15.1 0 0 0 6.6 6.6l2.2-2.2a1 1 0 0 1 1-.25 11.4 11.4 0 0 0 3.6.57 1 1 0 0 1 1 1V20a1 1 0 0 1-1 1A17 17 0 0 1 3 4a1 1 0 0 1 1-1h3.5a1 1 0 0 1 1 1c0 1.25.2 2.45.57 3.57a1 1 0 0 1-.25 1z"/></svg>
        <span>+36 30 555 0142</span>
      </div>
      <div class="contact-line">
        <svg viewBox="0 0 24 24"><path d="M2 5h20v14H2z M2 5l10 8 10-8" /></svg>
        <span>info@tabramley.hu</span>
      </div>
      <div class="contact-line">
        <svg viewBox="0 0 24 24"><circle cx="12" cy="12" r="10"/></svg>
        <span>www.tabramley.hu</span>
      </div>
    </div>
  </section>
</body>
</html>
```